Brand new letterhead, business card, email signature etc.

We are a financial company in London, UK. Our website is www.marlowvane.com. We're wanting a complete remodel of the company colours, letter head, business cards, email signatures, etc. Looking to keep the same font for the company name. I have upload a colour palette that we want to work with. We're looking for company letterhead for outgoing letters/ correspondence, letterhead for internal documentation, email signatures, e-letters. etc. Ultimately we will redesign the entire website also. It is important that our clients get a strong, secure, warm, trustworthy, solid feeling and first impression.
Updates

Designs look the same

Target Market(s)

Institutional investors, (ultra) high net worth individuals

Industry/Entity Type

Finance, Invesments banking.

Font styles to use
Other font styles liked:
• Current font is "Champagne & Limousines"

Requirements
Must have
• Must use the colours provided on the PDF uploaded to the portal. The purple = main colour. The red = accent colour.
Nice to have
• Nice to use same font as now for the company name "Corvane". Font is "Champagne & Limousines". Nice to have some reference to the old logo flower, but only subtle.
Should not have
• Do not use the colour red from our website. Use the colours provided on the colour palette PDF that I uploaded in the portal.

```html
<!DOCTYPE html>
<html lang="en">
<head>
<meta charset="utf-8">
<title>Corvane Email Signature</title>
<link rel="stylesheet" href="https://fonts.googleapis.com/css2?family=Didact+Gothic&family=Josefin+Sans:wght@300&display=swap">
<style>
  :root {
    --page: #ffffff;
    --paper: #fcfaf9;
    --frame: #8f8a8c;
    --mauve: #b9b1b3;
    --blush: #f2c9bb;
    --rule: #e3d6d2;
    --ink: #2b1e24;
    --name: #8a7a80;
    --accent: #e0241f;
    --icon: #ef9c86;
    --petal-grey: #cfc6c8;
    --petal-peach: #f3c7b2;
  }
  html, body {
    margin: 0; padding: 0;
    width: 1200px; height: 1000px;
    overflow: hidden;
    background: var(--page);
  }
  .signature {
    position: absolute;
    left: 342px; top: 413px;
    width: 514px; height: 171px;
    border: 1px solid var(--frame);
    background: var(--paper);
    overflow: hidden;
    font-family: "Didact Gothic", sans-serif;
    color: var(--ink);
  }
  .side-band { position: absolute; left: 0; top: 0; width: 20px; height: 100%; background: var(--mauve); }
  .side-line { position: absolute; left: 20px; top: 0; width: 3px; height: 100%; background: var(--blush); }
  .portrait {
    position: absolute; left: 18px; top: 26px;
    width: 88px; height: 116px;
    border: 2px solid var(--mauve);
    background: linear-gradient(160deg, #3a3f45 0%, #4d5a6e 45%, #2f4a72 100%);
  }
  .grid-line { position: absolute; background: var(--rule); }
  .brand {
    position: absolute; left: 137px; top: 16px;
    display: flex; align-items: center; gap: 8px;
  }
  .brand-square { width: 32px; height: 32px; border: 1px solid var(--name); box-sizing: border-box; }
  .brand-name {
    font-family: "Josefin Sans", sans-serif; font-weight: 300;
    font-size: 19px; letter-spacing: 2.5px; color: var(--name);
    text-transform: uppercase; line-height: 1;
  }
  .person-name {
    position: absolute; left: 137px; top: 73px;
    font-size: 13px; color: var(--name); letter-spacing: 0.2px;
  }
  .person-role {
    position: absolute; left: 137px; top: 91px;
    font-size: 8px; color: var(--accent);
  }
  .website { position: absolute; left: 327px; top: 77px; font-size: 9px; color: var(--ink); }
  .contacts { position: absolute; left: 123px; top: 117px; margin: 0; padding: 0; list-style: none; }
  .contacts li { display: flex; align-items: center; gap: 5px; height: 18px; font-size: 8.5px; color: var(--ink); }
  .contacts svg { width: 9px; height: 9px; flex: none; }
  .pattern {
    position: absolute; left: 427px; top: 0; width: 87px; height: 100%;
    border-left: 1px solid var(--rule);
  }
  .pattern-cell { position: absolute; left: 0; width: 100%; }
  .pattern-cell.upper {
    top: 0; height: 80px;
    background:
      radial-gradient(ellipse 60% 70% at 75% 35%, rgba(207,198,200,0.85), rgba(207,198,200,0) 70%),
      radial-gradient(ellipse 70% 60% at 20% 80%, rgba(207,198,200,0.5), rgba(207,198,200,0) 70%),
      #f7f3f3;
  }
  .pattern-cell.middle {
    top: 81px; height: 31px;
    background:
      radial-gradient(ellipse 70% 90% at 45% 90%, rgba(243,199,178,0.95), rgba(243,199,178,0) 75%),
      #fbefe9;
  }
  .pattern-cell.lower {
    top: 113px; height: 58px;
    background:
      radial-gradient(ellipse 65% 75% at 70% 55%, rgba(207,198,200,0.7), rgba(207,198,200,0) 70%),
      radial-gradient(ellipse 50% 60% at 20% 10%, rgba(243,199,178,0.45), rgba(243,199,178,0) 70%),
      #f7f3f3;
  }
</style>
</head>
<body>
  <section class="signature">
    <div class="side-band"></div>
    <div class="side-line"></div>
    <div class="portrait" role="img" aria-label="Portrait photo of Edwin Calloway"></div>

    <div class="grid-line" style="left:23px; top:145px; width:87px; height:1px;"></div>
    <div class="grid-line" style="left:70px; top:145px; width:1px; height:26px;"></div>
    <div class="grid-line" style="left:110px; top:112px; width:317px; height:1px;"></div>
    <div class="grid-line" style="left:110px; top:112px; width:1px; height:59px;"></div>

    <div class="brand">
      <span class="brand-square"></span>
      <span class="brand-name">Corvane</span>
    </div>

    <div class="person-name">EDWIN CALLOWAY</div>
    <div class="person-role">Chair of the Governing Body</div>
    <div class="website">www.marlowvane.com</div>

    <ul class="contacts">
      <li>
        <svg viewBox="0 0 10 10"><path d="M5 1a3 3 0 0 1 3 3c0 2-3 5-3 5S2 6 2 4a3 3 0 0 1 3-3z" fill="none" stroke="var(--icon)"/><circle cx="5" cy="4" r="1" fill="var(--icon)"/></svg>
        Corvane (IOM) Limited, Harbour Chambers, Ramsey, Isle of Man, IM98 2TD
      </li>
      <li>
        <svg viewBox="0 0 10 10"><rect x="2.5" y="1" width="5" height="8" rx="0.8" fill="none" stroke="var(--icon)"/><line x1="4" y1="7.5" x2="6" y2="7.5" stroke="var(--icon)"/></svg>
        Corvane Group Limited, 9th Floor, 14 Aldgate Row, London, EC3N 2QP
      </li>
      <li>
        <svg viewBox="0 0 10 10"><rect x="1" y="2.5" width="8" height="6" fill="none" stroke="var(--icon)"/><path d="M1 2.5l4 3 4-3" fill="none" stroke="var(--icon)"/></svg>
        info@corvane.com
      </li>
    </ul>

    <div class="pattern" role="img" aria-label="Soft line-drawn floral decoration in grey and peach">
      <div class="pattern-cell upper"></div>
      <div class="pattern-cell middle"></div>
      <div class="pattern-cell lower"></div>
    </div>
    <div class="grid-line" style="left:427px; top:80px; width:87px; height:1px;"></div>
    <div class="grid-line" style="left:427px; top:112px; width:87px; height:1px;"></div>
  </section>
</body>
</html>
```